Interior Stylist business card design needed

I need a business card for my new company in Sydney called "Liv Harrowby Designs". The business offers an interior styling and colour consultancy. My clients are generally not very design savvy (hence why they use me) and can range from being quite conservative to really wanting something "out there". They can be looking for a budget makeover or something more expensive / substantial. I'd like my business card design to be stylish (but not overly formal). I certainly don't want it to be conservative. I'd like it to stand out a bit! I don't really have any aversion to particular colours and I don't have a logo as such - my business name is really all I have.

Target Market(s)

As above - home owners, ranging from conservative to modern

Industry/Entity Type

Conservative

Contact Information for Business Card

Liv Harrowby Designs
Colour consultancy and interior styling
ph: 0417 238 605
email: livharrowby@qoralnet.net.au

Requirements
Should not have
• Old fashioned writing or motifs. No Times Roman font!!

```html
<!DOCTYPE html>
<html lang="en">
<head>
<meta charset="utf-8">
<title>Liv Harrowby Designs – Business Cards</title>
<link rel="stylesheet" href="https://fonts.googleapis.com/css2?family=Cinzel:wght@400;600&family=Open+Sans:wght@400&display=swap">
<style>
  :root {
    --backdrop: #e9e6e1;
    --charcoal: #3c3f3e;
    --gold: #c8952a;
    --soft-white: #e8e6e0;
    --card-w: 520px;
    --card-h: 298px;
  }
  * { box-sizing: border-box; margin: 0; padding: 0; }
  html, body { width: 1200px; height: 787px; overflow: hidden; }
  body {
    background: var(--backdrop);
    display: flex;
    align-items: center;
    justify-content: center;
    gap: 50px;
  }
  .card {
    position: relative;
    width: var(--card-w);
    height: var(--card-h);
    background: var(--charcoal);
    overflow: hidden;
    box-shadow: 0 6px 18px rgba(0,0,0,0.25);
  }
  .card__art { position: absolute; inset: 0; width: 100%; height: 100%; }

  /* Name side */
  .front__name {
    position: absolute;
    top: 118px; left: 0; right: 0;
    text-align: center;
    font-family: "Cinzel", serif;
    font-weight: 600;
    font-size: 30px;
    letter-spacing: 2px;
    color: var(--gold);
  }
  .front__web {
    position: absolute;
    top: 176px; left: 0; right: 0;
    text-align: center;
    font-family: "Open Sans", sans-serif;
    font-size: 11px;
    color: var(--gold);
  }

  /* Contact side */
  .back__name {
    position: absolute;
    top: 62px; left: 0; right: 0;
    text-align: center;
    font-family: "Cinzel", serif;
    font-weight: 600;
    font-size: 26px;
    letter-spacing: 1.5px;
    color: var(--gold);
  }
  .back__tagline {
    position: absolute;
    top: 100px; left: 0; right: 0;
    text-align: center;
    font-family: "Open Sans", sans-serif;
    font-size: 11px;
    letter-spacing: 9px;
    color: var(--soft-white);
  }
  .contact {
    position: absolute;
    left: 24px; top: 176px;
    list-style: none;
    font-family: "Open Sans", sans-serif;
    font-size: 11px;
    line-height: 18px;
    color: var(--charcoal);
  }
  .contact li { display: flex; align-items: center; gap: 7px; }
  .contact svg { width: 9px; height: 9px; flex: none; }
  .back__mark {
    position: absolute;
    right: 34px; top: 226px;
    font-family: "Cinzel", serif;
    font-weight: 600;
    font-size: 16px;
    letter-spacing: 1px;
    color: var(--charcoal);
  }
</style>
</head>
<body>

  <section class="card card--back" aria-label="Business card, contact side">
    <svg class="card__art" viewBox="0 0 520 298" aria-hidden="true">
      <polygon fill="var(--gold)" points="0,0 120,0 60,18 20,40 0,52"/>
      <polygon fill="var(--gold)" points="0,64 70,30 18,70 0,80"/>
      <polygon fill="var(--gold)" points="0,160 190,164 300,158 420,168 520,176 520,266 0,266"/>
      <polygon fill="var(--charcoal)" points="300,158 520,150 520,172 420,168"/>
      <rect x="0" y="266" width="520" height="32" fill="var(--charcoal)"/>
    </svg>
    <h1 class="back__name">Liv Harrowby</h1>
    <p class="back__tagline">DESIGNS</p>
    <ul class="contact">
      <li><svg viewBox="0 0 10 10"><rect width="10" height="10" fill="var(--charcoal)"/><path d="M3 2 L4.5 2 L5 4 L4 4.6 Q5 6.2 5.6 6.4 L6.4 5.4 L8 6 L8 7.6 Q4 8 2.4 3.2 Z" fill="var(--gold)"/></svg>0417 238 605</li>
      <li><svg viewBox="0 0 10 10"><rect width="10" height="10" fill="var(--charcoal)"/><path d="M2 3 H8 V7 H2 Z M2 3 L5 5.4 L8 3" fill="none" stroke="var(--gold)" stroke-width="0.8"/></svg>livharrowby@qoralnet.net.au</li>
      <li><svg viewBox="0 0 10 10"><rect width="10" height="10" fill="var(--charcoal)"/></svg>www.livharrowby.com/journal</li>
    </ul>
    <p class="back__mark">Liv Harrowby</p>
  </section>

  <section class="card card--front" aria-label="Business card, name side">
    <svg class="card__art" viewBox="0 0 520 298" aria-hidden="true">
      <path fill="var(--gold)" fill-rule="evenodd"
        d="M10,10 H510 V288 H10 Z
           M30,34 L140,28 L300,32 L470,26 L492,40 L488,150 L492,262 L380,268 L200,264 L48,270 L26,256 L30,150 Z"/>
      <polygon fill="var(--charcoal)" points="10,10 80,10 10,40"/>
      <polygon fill="var(--charcoal)" points="510,288 430,288 510,250"/>
    </svg>
    <h2 class="front__name">Liv Harrowby</h2>
    <p class="front__web">www.livharrowby.com</p>
  </section>

</body>
</html>
```